Wordpress Design Project for Bankruptcy Law Office in San Francisco

our current website: www.dorvanelilaw-example.com

we would like to re-design it for wordpress to make it faster and a bit more modern.

content should be similar to what we have there right now but also we do family law

please include logo for law office:

Law Office of Marta K. Dolvenidze

Thank you.
Updates

please see attached word document with logos that we like as an example.

we do tend to like color red.  darker red.

Please submit your design variations and logo as soon as possible.   We would like to go over them and make our decision

Reason: Please create couple of more variations of logo for your design, so we can make our decision what we like the most. Please see word doc for samples: Text: Law Office Of Marta K. Dolvenidze

Reason: final touches

Target Market(s)

bankruptcy and family law clients

Industry/Entity Type

Family Law

Requirements
Must have
• see examples of law sites
http://promo.lexorbin-example.com/testimonials

- new logo: Law Office of Marta K. Dolvenidze
- client intake form
- blog
- contact us form

Nice to have
• - map
- red color
- on the front page a nice photo of SF or a happy family

```html
<!DOCTYPE html>
<html lang="en">
<head>
<meta charset="utf-8">
<title>Dolvenidze Law</title>
<link rel="stylesheet" href="https://fonts.googleapis.com/css2?family=Source+Sans+3:ital,wght@0,400;0,600;1,400&display=swap">
<style>
:root{
  --page:#f5f5f5;
  --panel:#ffffff;
  --band:#e6e6e6;
  --brand:#3a6a96;
  --nav-top:#5b89b4;
  --nav-bottom:#3a6690;
  --text:#444444;
  --rule:#cfcfcf;
  --icon:#c9c9c9;
}
*{box-sizing:border-box;margin:0;padding:0}
html,body{width:1188px;height:1200px;overflow:hidden;background:var(--page)}
body{font-family:"Source Sans 3",Arial,sans-serif;color:var(--text)}
.stage{position:relative;width:1100px;height:1111px;transform:scale(1.08);transform-origin:0 0}
.abs{position:absolute}
.line{display:block;white-space:nowrap;text-align:justify;text-align-last:justify}
.line.last{text-align:left;text-align-last:left}
.top-bar{left:0;top:0;width:1100px;height:6px;background:var(--brand)}
.logo{left:68px;top:24px;font-size:40px;color:var(--brand);letter-spacing:-.5px}
.slogan{left:200px;top:76px;width:166px;text-align:right;font-size:12px;font-style:italic;color:#333}
.search{left:852px;top:50px;width:180px;height:25px;background:#fff;border:1px solid #cfcfcf;border-radius:2px;box-shadow:inset 0 1px 2px rgba(0,0,0,.08)}
.search span{position:absolute;left:14px;top:5px;font-size:11px;font-style:italic;color:#aaa}
.search svg{position:absolute;right:6px;top:6px}
.nav-band{left:0;top:126px;width:1100px;height:28px;background:var(--band)}
.nav{left:67px;top:114px;width:968px;height:51px;border-radius:3px;background:linear-gradient(var(--nav-top),var(--nav-bottom));display:flex;overflow:hidden;box-shadow:0 1px 2px rgba(0,0,0,.2)}
.nav a{display:flex;align-items:center;justify-content:center;color:#fff;text-decoration:none;font-size:14px;border-right:1px solid #2f5780;box-shadow:1px 0 0 rgba(255,255,255,.15)}
.nav a:last-child{border-right:0;box-shadow:none}
.nav a.active{background:linear-gradient(#7aa3c8,#5985af)}
.slider{left:67px;top:172px;width:968px;height:300px;border:2px solid #dcdcdc;background:linear-gradient(90deg,#bab0b0 0%,#a99d9c 45%,#6a5a55 75%,#3f332f 100%)}
.slider .photo{position:absolute;left:420px;top:20px;width:480px;height:276px;background:radial-gradient(ellipse at 50% 70%,rgba(110,60,30,.75),rgba(90,50,30,0) 70%)}
.slider .floor{position:absolute;left:0;bottom:0;width:100%;height:60px;background:linear-gradient(rgba(200,180,175,.2),rgba(120,70,50,.35))}
.slider h2{position:absolute;left:71px;top:74px;font-size:30px;font-weight:400;color:#2d2d2d}
.dots{position:absolute;left:26px;top:262px;display:flex;gap:11px}
.dots i{width:10px;height:10px;border-radius:50%;background:#3a3a3a}
.dots i:first-child{background:var(--brand)}
.content{left:67px;top:484px;width:968px;height:550px;background:var(--panel)}
.portrait{left:730px;top:492px;width:305px;height:275px;background:radial-gradient(ellipse at 45% 45%,#cfd3de 0%,#e8e9ef 45%,#fbfbfc 75%)}
.heading{font-size:20px;font-weight:400;color:var(--brand)}
.welcome-title{left:87px;top:507px}
.welcome-text{left:86px;top:547px;width:660px;font-size:13px;line-height:22px}
.bullets{list-style:none;font-size:12.5px;color:#333}
.bullets li{height:26px;display:flex;align-items:center;gap:13px}
.bullets-a{left:117px;top:670px}
.bullets-b{left:418px;top:670px}
.divider{left:87px;top:797px;width:928px;height:1px;background:var(--rule)}
.news-title{left:87px;top:820px}
.about-title{left:587px;top:820px}
.dotted{top:861px;height:0;border-top:2px dotted #9a9a9a}
.news-item{left:87px;width:466px;display:flex;gap:17px}
.news-item .icon{width:32px;height:32px;border-radius:50%;background:var(--icon);flex:none;margin-top:4px;display:flex;align-items:center;justify-content:center}
.news-item p{width:417px}
.small{font-size:12px;line-height:18px;color:#555}
.date{font-style:italic;color:var(--brand)}
.about-text{left:587px;top:882px;width:256px}
.view-more{left:587px;top:977px;font-size:12px;font-style:italic;color:var(--brand)}
.about-photo{left:859px;top:885px;width:156px;height:103px;border-radius:3px;background:radial-gradient(ellipse at 50% 50%,#b98d4d 0%,#d8b784 45%,#efdcbc 100%)}
.footer-links{left:67px;top:1051px;font-size:12px;color:#555}
.footer-links span{margin:0 7px;color:#888}
.copyright{left:67px;top:1075px;font-size:12px;color:#555}
.social{top:1057px;width:30px;height:30px;border-radius:50%;background:#b3b3b3}
</style>
</head>
<body>
<div class="stage">
  <div class="abs top-bar"></div>
  <div class="abs logo">DolvenidzeLaw</div>
  <div class="abs slogan">Company slogen goes here!</div>
  <div class="abs search"><span>Search</span>
    <svg width="12" height="12" viewBox="0 0 12 12"><circle cx="5" cy="5" r="3.6" fill="none" stroke="#aaa" stroke-width="1.3"/><line x1="7.7" y1="7.7" x2="11" y2="11" stroke="#aaa" stroke-width="1.5"/></svg>
  </div>
  <div class="abs nav-band"></div>
  <nav class="abs nav">
    <a class="active" style="width:101px">HOME</a>
    <a style="width:113px">ABOUT US</a>
    <a style="width:107px">LAWYERS</a>
    <a style="width:132px">LATEST NEWS</a>
    <a style="width:151px">LATEST ARTICLES</a>
    <a style="width:149px">PRACTICE AREAS</a>
    <a style="width:126px">CONTACT US</a>
    <a style="width:89px">FAQ</a>
  </nav>
  <section class="abs slider">
    <div class="photo" role="img" aria-label="Wooden judge's gavel resting on its sound block"></div>
    <div class="floor"></div>
    <h2>DUIS AUTE IRURE DOLOR</h2>
    <div class="dots"><i></i><i></i><i></i><i></i></div>
  </section>
  <div class="abs content"></div>
  <div class="abs portrait" role="img" aria-label="Smiling lawyer in shirt and tie leaning on a desk"></div>
  <h1 class="abs heading welcome-title">WELCOME TO OUR SITE</h1>
  <p class="abs welcome-text">
    <span class="line">Sed ut perspiciatis unde omnis iste natus error sit voluptatem accusantium doloremque laudantium, totam rem aperiam,</span>
    <span class="line">eaque ipsa quae ab illo inventore veritatis et quasi architecto beatae vitae dicta sunt explicabo. Nemo enim ipsam</span>
    <span class="line">voluptatem quia voluptas sit aspernatur aut odit aut fugit, sed quia consequuntur magni dolores eos qui ratione</span>
    <span class="line">voluptatem sequi nesciunt. Neque porro quisquam est, qui dolorem ipsum quia dolor sit amet, consectetur, adipisci velit,</span>
    <span class="line last">sed quia non numquam eius modi tempora incidunt ut labore et dolore magnam aliquam.</span>
  </p>
  <ul class="abs bullets bullets-a">
    <li><svg width="11" height="11" viewBox="0 0 11 11"><circle cx="5.5" cy="5.5" r="5.5" fill="#555"/><path d="M3 5.5h4M5.2 3.3l2.2 2.2-2.2 2.2" stroke="#fff" stroke-width="1.4" fill="none"/></svg>Duis accumsan aliquet arcu, vitae</li>
    <li><svg width="11" height="11" viewBox="0 0 11 11"><circle cx="5.5" cy="5.5" r="5.5" fill="#555"/><path d="M3 5.5h4M5.2 3.3l2.2 2.2-2.2 2.2" stroke="#fff" stroke-width="1.4" fill="none"/></svg>Morbi non lacus scelerisque nisl rhoncus</li>
    <li><svg width="11" height="11" viewBox="0 0 11 11"><circle cx="5.5" cy="5.5" r="5.5" fill="#555"/><path d="M3 5.5h4M5.2 3.3l2.2 2.2-2.2 2.2" stroke="#fff" stroke-width="1.4" fill="none"/></svg>Pellentesque pellentesque</li>
    <li><svg width="11" height="11" viewBox="0 0 11 11"><circle cx="5.5" cy="5.5" r="5.5" fill="#555"/><path d="M3 5.5h4M5.2 3.3l2.2 2.2-2.2 2.2" stroke="#fff" stroke-width="1.4" fill="none"/></svg>Cras venenatis massa ut orci pretium sit</li>
  </ul>
  <ul class="abs bullets bullets-b">
    <li><svg width="11" height="11" viewBox="0 0 11 11"><circle cx="5.5" cy="5.5" r="5.5" fill="#555"/><path d="M3 5.5h4M5.2 3.3l2.2 2.2-2.2 2.2" stroke="#fff" stroke-width="1.4" fill="none"/></svg>Duis accumsan aliquet arcu, vitae</li>
    <li><svg width="11" height="11" viewBox="0 0 11 11"><circle cx="5.5" cy="5.5" r="5.5" fill="#555"/><path d="M3 5.5h4M5.2 3.3l2.2 2.2-2.2 2.2" stroke="#fff" stroke-width="1.4" fill="none"/></svg>Morbi non lacus scelerisque nisl rhoncus</li>
    <li><svg width="11" height="11" viewBox="0 0 11 11"><circle cx="5.5" cy="5.5" r="5.5" fill="#555"/><path d="M3 5.5h4M5.2 3.3l2.2 2.2-2.2 2.2" stroke="#fff" stroke-width="1.4" fill="none"/></svg>Pellentesque pellentesque</li>
    <li><svg width="11" height="11" viewBox="0 0 11 11"><circle cx="5.5" cy="5.5" r="5.5" fill="#555"/><path d="M3 5.5h4M5.2 3.3l2.2 2.2-2.2 2.2" stroke="#fff" stroke-width="1.4" fill="none"/></svg>Cras venenatis massa ut orci pretium sit</li>
  </ul>
  <div class="abs divider"></div>

  <h2 class="abs heading news-title">LATEST NEWS</h2>
  <div class="abs dotted" style="left:87px;width:466px"></div>
  <article class="abs news-item" style="top:882px">
    <div class="icon"><svg width="16" height="16" viewBox="0 0 16 16"><rect x="1" y="1" width="11" height="11" fill="none" stroke="#fff" stroke-width="1.6"/><rect x="4" y="4" width="11" height="11" fill="#fff"/></svg></div>
    <p class="small">
      <span class="line">Sed ut perspiciatis unde omnis iste natus error sit voluptatem accusantium dolor</span>
      <span class="line">emque laudantium, totam rem aperiam, eaque ipsa quae ab illo inventore veritatis</span>
      <span class="line last date">August 29th, 2012</span>
    </p>
  </article>
  <article class="abs news-item" style="top:953px">
    <div class="icon"><svg width="16" height="16" viewBox="0 0 16 16"><rect x="1" y="1" width="11" height="11" fill="none" stroke="#fff" stroke-width="1.6"/><rect x="4" y="4" width="11" height="11" fill="#fff"/></svg></div>
    <p class="small">
      <span class="line">Sed ut perspiciatis unde omnis iste natus error sit voluptatem accusantium dolor</span>
      <span class="line">emque laudantium, totam rem aperiam, eaque ipsa quae ab illo inventore veritatis</span>
      <span class="line last date">August 29th, 2012</span>
    </p>
  </article>

  <h2 class="abs heading about-title">ABOUT US</h2>
  <div class="abs dotted" style="left:587px;width:428px"></div>
  <p class="abs small about-text">
    <span class="line">Sed ut perspiciatis unde omnis iste natus error sit</span>
    <span class="line">voluptatem accusantium dolor emque laudantium,</span>
    <span class="line">totam rem aperiam, eaque ipsa quae ab illo inven-</span>
    <span class="line">voluptatum deleniti atque corrupti quos dolores et</span>
    <span class="line">quas molestias excepturi sint occaecati cupiditate</span>
  </p>
  <a class="abs view-more">View more</a>
  <div class="abs about-photo" role="img" aria-label="Bronze statue of Lady Justice holding scales"></div>

  <div class="abs footer-links">Home<span>|</span>About us<span>|</span>Lawyers<span>|</span>Latest News<span>|</span>Latest Articles<span>|</span>Practice Areas<span>|</span>Contact us<span>|</span>FAQ</div>
  <div class="abs copyright">Copyright © 2012 www.dorvanelilaw-example.com &nbsp;&nbsp; All rights reserved.</div>
  <div class="abs social" style="left:949px" aria-label="Social link"></div>
  <div class="abs social" style="left:992px" aria-label="Social link"></div>
</div>
</body>
</html>
```